Business card design for my company.
I would like the card's background colour to be black. You can also see our web site to get an idea of our brand. https://www.tmwhomecrafting.com.au/
- Name
- Email

```html
<!DOCTYPE html>
<html lang="en">
<head>
<meta charset="utf-8">
<title>TMW Home Crafting – Business Card</title>
<link rel="stylesheet" href="https://fonts.googleapis.com/css2?family=Montserrat:wght@400;500;700&display=swap">
<style>
  :root {
    --stage: #3a3a3a;
    --card-black: #151515;
    --brand-green: #07954a;
    --ink-white: #f4f4f4;
    --font-main: "Montserrat", Arial, sans-serif;
  }
  * { box-sizing: border-box; margin: 0; padding: 0; }
  html, body {
    width: 1200px;
    height: 689px;
    overflow: hidden;
    background: var(--stage);
    font-family: var(--font-main);
  }
  .sheet {
    position: relative;
    width: 1200px;
    height: 689px;
    display: flex;
    align-items: center;
    justify-content: center;
    gap: 60px;
  }
  .card {
    position: relative;
    width: 520px;
    height: 318px;
    border-radius: 22px;
    overflow: hidden;
  }
  .card--front {
    background: var(--brand-green);
    display: flex;
    align-items: center;
    justify-content: center;
  }
  .card--back {
    background: var(--card-black);
  }
  .brand-name {
    display: flex;
    align-items: center;
    gap: 14px;
    color: var(--ink-white);
    font-weight: 700;
    letter-spacing: 0.06em;
    text-transform: uppercase;
    white-space: nowrap;
  }
  .brand-name__square {
    width: 22px;
    height: 22px;
    background: var(--ink-white);
    flex: none;
  }
  .card--front .brand-name { font-size: 34px; }
  .card--back .brand-name {
    position: absolute;
    left: 34px;
    top: 222px;
    font-size: 21px;
    gap: 10px;
  }
  .card--back .brand-name__square { width: 14px; height: 14px; }
  .divider {
    position: absolute;
    left: 246px;
    top: 64px;
    width: 2px;
    height: 116px;
    background: var(--brand-green);
  }
  .contact {
    position: absolute;
    left: 266px;
    top: 70px;
    right: 36px;
    color: var(--ink-white);
  }
  .contact__name {
    color: var(--brand-green);
    font-weight: 700;
    font-size: 25px;
    line-height: 1.1;
    white-space: nowrap;
  }
  .contact__title {
    font-weight: 400;
    font-size: 14px;
    margin-top: 6px;
  }
  .contact__email {
    display: flex;
    align-items: center;
    gap: 7px;
    font-size: 11.5px;
    margin-top: 22px;
    white-space: nowrap;
  }
  .contact__email svg { flex: none; }
</style>
</head>
<body>
  <main class="sheet">
    <section class="card card--front" aria-label="Card front">
      <div class="brand-name"><span class="brand-name__square"></span>TMW Home Crafting</div>
    </section>

    <section class="card card--back" aria-label="Card back">
      <div class="brand-name"><span class="brand-name__square"></span>TMW Home Crafting</div>
      <div class="divider"></div>
      <div class="contact">
        <p class="contact__name">Liam Harcourt</p>
        <p class="contact__title">General Manager</p>
        <p class="contact__email">
          <svg width="14" height="10" viewBox="0 0 14 10" aria-hidden="true">
            <rect x="0.5" y="0.5" width="13" height="9" fill="var(--brand-green)"/>
            <path d="M0.5 0.5 L7 5.5 L13.5 0.5" fill="none" stroke="var(--card-black)" stroke-width="1"/>
          </svg>
          info@tmwhomecrafting.com.au
        </p>
      </div>
    </section>
  </main>
</body>
</html>
```